TL - business card

Tallow Partners is an insurance brokerage firm, inovative, proactive, vigorous, which aims to become the leader of the insurance brokers in Anfrica. We should like to get some designs which should be avoided also in Gray / Metallic for the Administration and Orange / Blue for the Managers (ike in the picture sent). The Blue / Green logo is not the correct one, but the source of the file. Please adjust the color accordingly for the business cards. 1 / Orange / Blue 2 / Gray / Metallic We want something classic but which is transmitted strenght, inovation, modernity and most of all, rapidity. We want something start-up like, very punchy and catching eye remaining profesional at the same time. Name: Dorian Whitlock Function: Managing Director Address: N ° 17/18 Rua Veloso - R / C 2B Direita - Bairro Mutamba - Luanda Tel: (+244) 947 582 316 Email: dorian.whitlock@tallow-p.example Website: www.tallow-p. example We want classic in the front and creative, colorfull at the back. The cards will be printed in relief, with very high quality of paper.
Insurance Broker
Colors
Designer to choose colors to be used in the design.

```html
<!DOCTYPE html>
<html lang="en">
<head>
<meta charset="utf-8">
<title>Tallow Partners – Business Card</title>
<link rel="stylesheet" href="https://fonts.googleapis.com/css2?family=Exo+2:wght@500;600&family=Lato:wght@400&display=swap">
<style>
  :root {
    --backdrop: #2b2b2d;
    --card: #121212;
    --card-edge: #1a1a1a;
    --orange: #f26a1b;
    --blue: #29a8e0;
    --text: #e6e6e6;
    --muted: #bfbfbf;
  }
  * { box-sizing: border-box; margin: 0; padding: 0; }
  html, body {
    width: 1200px;
    height: 900px;
    overflow: hidden;
    background: var(--backdrop);
  }
  .canvas {
    position: relative;
    width: 1200px;
    height: 900px;
    display: flex;
    flex-direction: column;
    align-items: center;
    justify-content: center;
    gap: 56px;
  }
  .card {
    position: relative;
    width: 600px;
    height: 343px;
    background: linear-gradient(160deg, var(--card-edge), var(--card));
    box-shadow: 0 14px 30px rgba(0, 0, 0, 0.45);
    overflow: hidden;
  }
  .card__stripe {
    position: absolute;
    left: 0;
    right: 0;
    bottom: 0;
    height: 7px;
    background: linear-gradient(90deg, var(--orange) 0%, var(--orange) 42%, var(--blue) 58%, var(--blue) 100%);
  }

  /* Front */
  .front__brand {
    position: absolute;
    inset: 0 0 7px 0;
    display: flex;
    align-items: center;
    justify-content: center;
    gap: 16px;
  }
  .brand__dot {
    width: 34px;
    height: 34px;
    border-radius: 50%;
    background: var(--orange);
  }
  .brand__name {
    font-family: "Exo 2", sans-serif;
    font-weight: 600;
    font-size: 36px;
    letter-spacing: 1px;
    text-transform: uppercase;
    color: var(--blue);
  }

  /* Back */
  .back__identity {
    position: absolute;
    top: 110px;
    left: 0;
    width: 600px;
    display: flex;
    align-items: center;
    justify-content: center;
    gap: 18px;
  }
  .person {
    text-align: right;
  }
  .person__name {
    font-family: "Exo 2", sans-serif;
    font-weight: 500;
    font-size: 23px;
    text-transform: uppercase;
    letter-spacing: 0.5px;
    line-height: 1.05;
  }
  .person__first { color: var(--orange); }
  .person__last { color: var(--blue); }
  .person__role {
    font-family: "Lato", sans-serif;
    font-size: 15px;
    color: var(--text);
  }
  .divider {
    width: 1px;
    height: 46px;
    background: var(--muted);
  }
  .contact {
    list-style: none;
    font-family: "Lato", sans-serif;
    font-size: 15px;
    color: var(--text);
    display: flex;
    flex-direction: column;
    gap: 4px;
  }
  .contact__item {
    display: flex;
    align-items: center;
    gap: 7px;
  }
  .contact__icon {
    width: 14px;
    height: 14px;
    flex: none;
  }
  .address {
    position: absolute;
    top: 208px;
    left: 0;
    width: 600px;
    text-align: center;
    font-family: "Lato", sans-serif;
    font-size: 15px;
    line-height: 1.35;
    color: var(--text);
  }
</style>
</head>
<body>
<main class="canvas">
  <section class="card card--front" aria-label="Card front">
    <div class="front__brand">
      <span class="brand__dot"></span>
      <span class="brand__name">Tallow Partners</span>
    </div>
    <div class="card__stripe"></div>
  </section>

  <section class="card card--back" aria-label="Card back">
    <div class="back__identity">
      <div class="person">
        <p class="person__name"><span class="person__first">Dorian</span> <span class="person__last">Whitlock</span></p>
        <p class="person__role">Managing Director</p>
      </div>
      <span class="divider"></span>
      <ul class="contact">
        <li class="contact__item">
          <svg class="contact__icon" viewBox="0 0 16 16" aria-hidden="true">
            <path fill="#f26a1b" d="M3.2 1.5l2.4-.4 1.5 3.3-1.6 1.2c.8 1.8 2.1 3.1 3.9 3.9l1.2-1.6 3.3 1.5-.4 2.4c-.2.9-1 1.4-1.9 1.3C6 12.5 2.9 9.4 2.4 3.4c-.1-.9.4-1.7.8-1.9z"/>
          </svg>
          <span>(+244) 947 582 316</span>
        </li>
        <li class="contact__item">
          <svg class="contact__icon" viewBox="0 0 16 16" aria-hidden="true">
            <rect x="1" y="3" width="14" height="10" rx="1" fill="#f26a1b"/>
            <path d="M1.5 3.8L8 9l6.5-5.2" fill="none" stroke="#121212" stroke-width="1.3"/>
          </svg>
          <span>dorian.whitlock@tallow-p.example</span>
        </li>
      </ul>
    </div>
    <address class="address" style="font-style: normal;">
      N ° 17/18 Rua Veloso - R / C 2B Direita<br>
      Bairro Mutamba - Luanda
    </address>
    <div class="card__stripe"></div>
  </section>
</main>
</body>
</html>
```